Stationery Design Project for Kerbilo, Chicago

Kerbilo, a street parking application which helps car drivers find a street parking spot by offering an ideal path along which to look for parking. This path is calculated by our algorithm based on data (e.g. historical data, baseball games schedule, etc.). Along this path the driver will find a spot and will also save 70% of the search time. Customer we target is reg. between 21 and 45 yo.

We envision something young, fresh, bright and original. Slightly abstract maybe. It should represent the idea and elements of finding street parking in the city, e.g. car(s), parking spot, people, city, etc. (just ideas!).

Logo is attached.

Requirement:
- Business Cards (2 Sided Full Color CMYK)
- Letterhead (1 Sided Full Color CMYK)
- Envelope (1 Sided Full Color CMYK)
- Sticker (1 Sided Full Color CMYK), round with a 2inch diameter.

Reason: We're starting to get more and more designs and need more time to look into all of them. Very exciting!! Thanks to everybody!

Hi all, we're in the process of selecting our favs. Though choices!!! Really good submissions. Will keep you posted and sorry for the delay.

Target Market(s)

Car drivers and owners between 21 and 45

Industry/Entity Type

Parking

Requirements
Must have
• Sticker should be round and include company URL kerbilo.com and the new logo which we will attach soon.
Should not have
• Should not be too serious or boring.

```html
<!DOCTYPE html>
<html lang="en">
<head>
<meta charset="utf-8">
<title>Kerbilo business card</title>
<link href="https://fonts.googleapis.com/css2?family=Open+Sans:wght@400;600;700&display=swap" rel="stylesheet">
<style>
  :root {
    --backdrop: #b48d2e;
    --card: #ffffff;
    --ink: #1c1c1c;
    --text: #2a2a2a;
    --accent: #1a8fd3;
    --blue-deep: #1f3fb0;
    --blue-bright: #1f8fe6;
    --band-dark: #2c2c2c;
    --band-light: #8a8a8a;
    --mark: #2a63c9;
  }
  * { box-sizing: border-box; margin: 0; padding: 0; }
  html, body { width: 1200px; height: 686px; overflow: hidden; }
  body {
    position: relative;
    background: var(--backdrop);
    font-family: "Open Sans", Arial, sans-serif;
    color: var(--text);
  }
  .card {
    position: absolute;
    width: 510px;
    height: 291px;
    background: var(--card);
    border-radius: 22px;
    overflow: hidden;
  }
  .card--front { left: 77px; top: 129px; }
  .card--back { left: 624px; top: 255px; }

  .corner-band { position: absolute; left: 0; top: 0; width: 200px; height: 190px; }

  .brand { position: absolute; display: flex; align-items: center; }
  .brand__dot {
    border-radius: 50%;
    background: var(--mark);
    border: 6px solid var(--card);
    box-shadow: 0 0 0 1px #d8d8d8;
    flex: none;
  }
  .brand__name {
    font-weight: 600;
    color: var(--ink);
    letter-spacing: 0.5px;
    line-height: 1;
  }
  .card--front .brand { left: 53px; top: 50px; }
  .card--front .brand__dot { width: 90px; height: 90px; }
  .card--front .brand__name { font-size: 44px; margin-left: 8px; margin-top: -6px; }
  .card--back .brand { left: 98px; top: 98px; }
  .card--back .brand__dot { width: 94px; height: 94px; }
  .card--back .brand__name { font-size: 46px; margin-left: 14px; margin-top: -4px; }

  .holder { position: absolute; left: 152px; top: 138px; font-size: 12px; font-weight: 700; color: #2a2418; }
  .holder__name { font-size: 15.5px; color: var(--accent); }

  .contacts { position: absolute; left: 150px; top: 168px; list-style: none; font-size: 12px; }
  .contacts li { display: flex; align-items: center; height: 17.5px; }
  .contacts li:nth-child(2) { margin-top: 4px; }
  .contacts svg { width: 12px; height: 12px; margin-right: 3px; fill: var(--accent); flex: none; }
  .address { position: absolute; left: 151px; top: 250px; font-size: 12px; }
</style>
</head>
<body>

<section class="card card--front">
  <svg class="corner-band" viewBox="0 0 200 190" aria-hidden="true">
    <defs>
      <linearGradient id="corner-blue" x1="0" y1="0" x2="1" y2="1">
        <stop offset="0" stop-color="#1f3fb0"/>
        <stop offset="1" stop-color="#1f8fe6"/>
      </linearGradient>
      <linearGradient id="band-grey" x1="0" y1="0" x2="1" y2="1">
        <stop offset="0" stop-color="#8a8a8a"/>
        <stop offset="1" stop-color="#2c2c2c"/>
      </linearGradient>
    </defs>
    <path d="M0 0 H155 C120 70 60 115 0 146 Z" fill="url(#corner-blue)"/>
    <path d="M162 0 H180 C140 85 70 150 0 182 V156 C65 122 128 72 162 0 Z" fill="url(#band-grey)"/>
  </svg>

  <div class="brand">
    <span class="brand__dot"></span>
    <span class="brand__name">Kerbilo</span>
  </div>

  <p class="holder"><span class="holder__name">Your Name</span>, Title</p>

  <ul class="contacts">
    <li><svg viewBox="0 0 24 24"><path d="M6.6 10.8a15 15 0 0 0 6.6 6.6l2.2-2.2c.3-.3.7-.4 1-.2 1.1.4 2.3.6 3.6.6.6 0 1 .4 1 1V20c0 .6-.4 1-1 1A17 17 0 0 1 3 4c0-.6.4-1 1-1h3.5c.6 0 1 .4 1 1 0 1.3.2 2.5.6 3.6.1.3 0 .7-.2 1z"/></svg>123-456-7890</li>
    <li><svg viewBox="0 0 24 24"><path d="M6 2h10v6H6zM3 9h18v9h-3v4H6v-4H3zm5 7v4h8v-4z"/></svg>123-456-7890</li>
    <li><svg viewBox="0 0 24 24"><path d="M2 5h20v14H2zm2 2v.5l8 5 8-5V7z"/></svg>name@website.com</li>
    <li><svg viewBox="0 0 24 24"><path d="M12 2a10 10 0 1 0 0 20 10 10 0 0 0 0-20zm0 2c.9 1.2 1.5 2.5 1.9 4h-3.8c.4-1.5 1-2.8 1.9-4zM4.3 14a8 8 0 0 1 0-4h3.4a16 16 0 0 0 0 4zm8.7 6c-.9-1.2-1.5-2.5-1.9-4h3.8c-.4 1.5-1 2.8-1.9 4zm1.3-6H9.7a14 14 0 0 1 0-4h4.6a14 14 0 0 1 0 4zm2 0a16 16 0 0 0 0-4h3.4a8 8 0 0 1 0 4z"/></svg>www.kerbilo.com</li>
  </ul>

  <p class="address">Street name City State, zip code</p>
</section>

<section class="card card--back">
  <div class="brand">
    <span class="brand__dot"></span>
    <span class="brand__name">Kerbilo</span>
  </div>
</section>

</body>
</html>
```